Redesign a Start-Up Dating Website

Website: https://morvelique.com.
Make sure the design has an island style theme.
I would like the 7 pages of my website to have a new and professional look. I want the same colors to remain, but I want a creative look for all the pages. This is a dating website that is in the startup stage. So, I want to give my entire website a custom makeover. I want something that will stand out from the other dating sites. Something that will attract more people to want to use my services, and hopefully get new members.
Target Market(s)
Dating
Industry/Entity Type
Dating
Coding
Coded - Design and coding required
Number of Pages Required
5+ page
Font styles to use
Other font styles liked:
- Decorative, San Serif
Requirements
Must have
- The design must have the original colors and a stylish font to go along. The design must be creative, welcoming, and professional. I would like an island style theme for the website. This is a dating website so make sure that the design is tailored to that aspect.
Nice to have
- It would be nice to have a decorative font and a professional style on all the pages. Make sure the design will be mobile responsive and friendly for all the pages on the website.
Should not have
- The design should not be bland and uncreative.

```html
<!DOCTYPE html>
<html lang="en">
<head>
<meta charset="utf-8">
<title>Morvelique – Members</title>
<link href="https://fonts.googleapis.com/css2?family=Open+Sans:wght@400;600;700&family=Raleway:wght@600;700;800&display=swap" rel="stylesheet">
<style>
:root{
  --teal:#2bb3a6;
  --orange:#f7941d;
  --ink:#333;
  --muted:#777;
  --line:#d9d9d9;
  --tab:#9a9a9a;
  --footer:#f2f2f2;
  --white:#fff;
}
*{box-sizing:border-box;margin:0;padding:0}
html,body{width:668px;height:1200px;overflow:hidden;background:var(--white)}
body{font-family:"Open Sans",Arial,sans-serif;color:var(--ink);position:relative}
.site-header{height:46px;display:flex;align-items:center;justify-content:space-between;padding:0 40px 0 48px}
.brand{display:flex;align-items:center;gap:6px;font-family:"Raleway",sans-serif;font-weight:700;font-size:19px;color:var(--teal)}
.brand-dot{width:18px;height:18px;border-radius:50%;background:var(--orange)}
.main-nav{display:flex;align-items:center;gap:12px;font-size:8.5px;font-weight:700;letter-spacing:.3px}
.main-nav a{color:var(--ink);text-decoration:none}
.main-nav a.active{color:var(--orange)}
.btn-login{background:var(--orange);color:var(--white)!important;border-radius:12px;padding:5px 10px}
.hero{height:164px;position:relative;display:flex;align-items:center;justify-content:center;
  background:linear-gradient(180deg,#9aa8b6 0%,#c7b7a8 55%,#7f8a92 100%)}
.hero h1{font-family:"Raleway",sans-serif;font-weight:800;font-size:38px;color:var(--white);letter-spacing:1px;position:relative}
.breadcrumb{margin:14px 48px 0;padding-bottom:6px;border-bottom:1px solid var(--line);font-size:7px;font-weight:700}
.breadcrumb span{color:var(--orange)}
.tabs{display:flex;justify-content:center;gap:8px;margin-top:50px}
.tab{width:72px;height:22px;display:flex;align-items:center;justify-content:center;background:var(--tab);color:var(--white);font-size:8px;font-weight:700;border-radius:3px 3px 0 0}
.tab.active{background:var(--teal)}
.register-form{margin:0 auto;width:502px;height:398px;border:1px solid var(--line);border-top:3px solid var(--teal);padding:30px 0 0}
.field{display:flex;align-items:center;margin-bottom:12px;padding-left:38px}
.field label{width:56px;font-size:7px;font-weight:700}
.input{width:150px;height:22px;border:1px solid var(--line);border-radius:2px;margin-left:-14px;margin-left:0}
.field .input{margin-left:-2px;width:150px}
.field .input.wide{width:150px}
.field .box{width:150px;height:22px;border:1px solid var(--line)}
.row-input{width:150px}
.field{padding-left:45px}
.field label{width:47px}
.full{width:152px}
.form-input{width:150px;height:22px;border:1px solid var(--line);margin-left:0}
.form-input.long{width:150px}
.long{width:150px}
.field .ctrl{width:150px;height:22px;border:1px solid var(--line);border-radius:2px;position:relative;font-size:6.5px;color:var(--muted);display:flex;align-items:center;padding-left:5px}
.field .ctrl.big{width:150px}
.ctrl.full-w{width:150px}
.wide-ctrl{width:150px}
.field .ctrl{width:150px}
.field .ctrl.xl{width:150px}
.field .ctrl.stretch{width:150px}
.selects{display:flex;gap:5px}
.field .ctrl.sm{width:47px}
.caret{position:absolute;right:0;top:0;width:18px;height:100%;border-left:1px solid var(--line);display:flex;align-items:center;justify-content:center}
.check{display:flex;align-items:center;gap:6px;padding-left:92px;font-size:7px;margin-top:6px}
.check i{width:8px;height:8px;border:1px solid #999;display:block}
.btn{display:block;margin:16px auto 0;width:72px;height:24px;border-radius:12px;background:var(--orange);color:var(--white);font-size:7.5px;font-weight:700;display:flex;align-items:center;justify-content:center}
.community{text-align:center;margin-top:48px}
.community h2{font-family:"Raleway",sans-serif;font-weight:800;font-size:13.5px}
.members{display:flex;justify-content:center;align-items:flex-start;gap:20px;margin-top:22px;position:relative}
.member{width:88px;text-align:center}
.avatar{width:88px;height:88px;border-radius:50%;border:3px solid var(--white);box-shadow:0 0 0 1px var(--line);margin:10px auto 0}
.member.feature{width:102px}
.member.feature .avatar{width:102px;height:102px;margin-top:0}
.name{font-size:7.5px;font-weight:700;margin-top:10px}
.place{font-size:6.5px;color:var(--teal);font-style:italic;margin-top:2px}
.arrow{position:absolute;top:45px;font-size:14px;color:#aaa}
.join{margin-top:22px}
.site-footer{position:absolute;left:0;right:0;bottom:0;height:150px;background:var(--footer);border-top:3px solid var(--teal)}
.contact-row{display:flex;justify-content:center;gap:60px;margin-top:22px;font-size:6.5px;color:var(--muted)}
.contact{display:flex;align-items:center;gap:8px}
.ico{width:20px;height:20px;border-radius:50%;background:var(--orange);display:flex;align-items:center;justify-content:center}
.foot-links{text-align:center;font-size:6.5px;color:var(--muted);margin-top:28px}
.bottom{display:flex;justify-content:space-between;align-items:center;margin:22px 48px 0;padding-top:8px;border-top:1px solid var(--line);font-size:6px;color:var(--muted)}
.social{display:flex;gap:4px}
.social i{display:block;width:12px;height:12px;border-radius:50%;border:1px solid var(--orange)}
</style>
</head>
<body>
<header class="site-header">
  <div class="brand"><span class="brand-dot"></span>Morvelique</div>
  <nav class="main-nav">
    <a href="#">HOME</a><a href="#">SEARCH</a><a class="active" href="#">MEMBERS</a><a href="#">EXTRAS</a><a href="#">ABOUT</a><a href="#">PREMIUM</a><a href="#">CONTACT</a><a class="btn-login" href="#">LOGIN</a>
  </nav>
</header>

<section class="hero" role="img" aria-label="Couple holding hands on a beach at sunset">
  <h1>MEMBERS</h1>
</section>

<div class="breadcrumb">HOME &raquo; <span>MEMBERS</span></div>

<div class="tabs">
  <div class="tab active">REGISTER</div><div class="tab">STORIES</div><div class="tab">ONLINE</div><div class="tab">SEARCH</div>
</div>

<form class="register-form">
  <div class="field"><label>USERNAME:</label><div class="ctrl" style="width:300px"></div></div>
  <div class="field"><label>PASSWORD:</label><div class="ctrl" style="width:300px"></div></div>
  <div class="field"><label>CONFIRM PASSWORD:</label><div class="ctrl" style="width:300px"></div></div>
  <div class="field"><label>EMAIL:</label><div class="ctrl" style="width:300px"></div></div>
  <div class="field"><label>CONFIRM EMAIL:</label><div class="ctrl" style="width:300px"></div></div>
  <div class="field"><label>GENDER</label><div class="ctrl" style="width:300px"><span class="caret">&#9662;</span></div></div>
  <div class="field"><label>BIRTH DATE</label>
    <div class="selects">
      <div class="ctrl" style="width:96px">January<span class="caret">&#9662;</span></div>
      <div class="ctrl" style="width:96px">1<span class="caret">&#9662;</span></div>
      <div class="ctrl" style="width:98px">2017<span class="caret">&#9662;</span></div>
    </div>
  </div>
  <div class="check"><i></i>I agree to the Terms and Conditions</div>
  <div class="btn">REGISTER</div>
</form>

<section class="community">
  <h2>JOIN THIS COMMUNITY OF 1 MORVELIQUE MEMBERS</h2>
  <div class="members">
    <span class="arrow" style="left:26px">&#8249;</span>
    <div class="member"><div class="avatar" role="img" aria-label="Member photo" style="background:linear-gradient(135deg,#c98a7a,#6b4a44)"></div><div class="name">TAVRELO</div><div class="place">42, Germany</div></div>
    <div class="member"><div class="avatar" role="img" aria-label="Member photo" style="background:linear-gradient(135deg,#8a6a55,#3a2a22)"></div><div class="name">OLWENNA</div><div class="place">28, United States</div></div>
    <div class="member feature"><div class="avatar" role="img" aria-label="Member photo" style="background:linear-gradient(135deg,#b08060,#4a3020)"></div><div class="name">MIRELLE</div><div class="place">23, United States</div></div>
    <div class="member"><div class="avatar" role="img" aria-label="Member photo" style="background:linear-gradient(135deg,#c9a58a,#7a6050)"></div><div class="name">DARIOK</div><div class="place">27, Canada</div></div>
    <div class="member"><div class="avatar" role="img" aria-label="Member photo" style="background:linear-gradient(135deg,#d0b8a8,#8a7060)"></div><div class="name">QUESSA</div><div class="place">26, United States</div></div>
    <span class="arrow" style="right:26px">&#8250;</span>
  </div>
  <div class="btn join">JOIN US FREE</div>
</section>

<footer class="site-footer">
  <div class="contact-row">
    <div class="contact"><span class="ico"><svg width="10" height="10" viewBox="0 0 10 10"><path d="M5 1a3 3 0 0 1 3 3c0 2-3 5-3 5S2 6 2 4a3 3 0 0 1 3-3z" fill="#fff"/></svg></span><span>Morvelique Dating<br>Contact | Morvelique | Dating Easy</span></div>
    <div class="contact"><span class="ico"><svg width="10" height="10" viewBox="0 0 10 10"><path d="M2 1h2l1 2-1 1a5 5 0 0 0 2 2l1-1 2 1v2c-4 0-7-3-7-7z" fill="#fff"/></svg></span><span>1-800-555-0142</span></div>
    <div class="contact"><span class="ico"><svg width="10" height="10" viewBox="0 0 10 10"><rect x="1" y="2.5" width="8" height="5" fill="none" stroke="#fff"/><path d="M1 2.5l4 3 4-3" fill="none" stroke="#fff"/></svg></span><span>contact@morvelique.com</span></div>
  </div>
  <div class="foot-links">Morvelique &nbsp;|&nbsp; About &nbsp;|&nbsp; Contact &nbsp;|&nbsp; Login &nbsp;|&nbsp; Members &nbsp;|&nbsp; Premium &nbsp;|&nbsp; Register &nbsp;|&nbsp; Search</div>
  <div class="bottom"><span>Copyright © 2017. Morvelique. All rights reserved.</span><div class="social"><i></i><i></i><i></i><i></i></div></div>
</footer>
</body>
</html>
```